Need to create logo for Harbourline Ventures Ltd

We supply the above mention products all around NZ. Trading under the company name Harbourline Ventures Ltd.

Industry/Entity Type

It Company

Contact Information for Business Card

Harbourline Ventures Ltd. 0800519203 0217043952 Brent@Talvora.co.nz contact Brent HOLM
Suppliers of Talvora Louvres, Aluminim Sable shutters, Fennroll curtains,Glow forge outdoor heaters,Caltex outdoor heaters

```html
<!DOCTYPE html>
<html lang="en">
<head>
<meta charset="utf-8">
<title>Harbourline Ventures Ltd — Business Card</title>
<link rel="stylesheet" href="https://fonts.googleapis.com/css2?family=Cinzel:wght@400&family=Open+Sans:wght@400;600&display=swap">
<style>
  :root {
    --canvas-bg: #e9e6e1;
    --card-light: #ffffff;
    --card-dark: #050505;
    --ink-dark: #111111;
    --ink-light: #f2f2f2;
    --rule-dark: #1a1a1a;
    --rule-light: #d8d8d8;
  }
  * { margin: 0; padding: 0; box-sizing: border-box; }
  html, body {
    width: 1200px; height: 892px; overflow: hidden;
    background: var(--canvas-bg);
  }
  .canvas {
    position: relative; width: 1200px; height: 892px;
    display: flex; align-items: center; justify-content: center; gap: 40px;
  }
  .card {
    position: relative; width: 540px; height: 310px;
    border-radius: 14px; overflow: hidden;
    box-shadow: 0 6px 18px rgba(0,0,0,0.18);
  }
  .card-front { background: var(--card-light); color: var(--ink-dark); }
  .card-back { background: var(--card-dark); color: var(--ink-light); }

  .company-name {
    position: absolute; left: 34px; top: 60px;
    font-family: "Cinzel", serif; font-size: 30px; font-weight: 400;
    letter-spacing: 0.3px; white-space: nowrap;
  }
  .name-rule {
    position: absolute; left: 0; top: 146px; width: 348px; height: 2px;
    background: var(--rule-dark);
  }
  .contact-name {
    position: absolute; left: 358px; top: 128px;
    font-family: "Open Sans", sans-serif; font-size: 22px; font-weight: 400;
    letter-spacing: 0.5px; white-space: nowrap;
  }
  .contact-list {
    position: absolute; left: 40px; top: 182px; list-style: none;
    font-family: "Open Sans", sans-serif; font-size: 17px;
  }
  .contact-item { display: flex; align-items: center; height: 34px; gap: 14px; }
  .contact-icon { width: 16px; height: 16px; flex: none; }

  .services-title {
    position: absolute; left: 38px; top: 40px;
    font-family: "Open Sans", sans-serif; font-size: 30px; font-weight: 400;
  }
  .services-rule {
    position: absolute; left: 156px; top: 68px; right: 24px; height: 2px;
    background: var(--rule-light);
  }
  .services-list {
    position: absolute; left: 44px; top: 100px; list-style: none;
    font-family: "Open Sans", sans-serif; font-size: 18px; font-weight: 400;
  }
  .service-item { display: flex; align-items: center; height: 36px; gap: 14px; }
  .service-bullet { width: 12px; height: 12px; flex: none; }
</style>
</head>
<body>
<main class="canvas">
  <section class="card card-front" aria-label="Business card front">
    <h1 class="company-name">Harbourline Ventures Ltd</h1>
    <div class="name-rule"></div>
    <p class="contact-name">Brent HOLM</p>
    <ul class="contact-list">
      <li class="contact-item">
        <svg class="contact-icon" viewBox="0 0 16 16" aria-hidden="true"><rect width="16" height="16" fill="#111"/><path d="M5 3.5l1.6 2.2-1 1.1c.7 1.4 1.8 2.5 3.2 3.2l1.1-1 2.2 1.6-.8 1.7c-3.8-.3-7.4-3.9-7.7-7.7z" fill="#fff"/></svg>
        <span>0800 519 203</span>
      </li>
      <li class="contact-item">
        <svg class="contact-icon" viewBox="0 0 16 16" aria-hidden="true"><rect width="16" height="16" fill="#111"/><rect x="5" y="3" width="6" height="10" rx="1" fill="none" stroke="#fff" stroke-width="1.2"/><line x1="7" y1="11.3" x2="9" y2="11.3" stroke="#fff"/></svg>
        <span>0217 043 952</span>
      </li>
      <li class="contact-item">
        <svg class="contact-icon" viewBox="0 0 16 16" aria-hidden="true"><rect width="16" height="16" fill="#111"/><rect x="3" y="4.5" width="10" height="7" fill="none" stroke="#fff" stroke-width="1.2"/><path d="M3 4.5l5 4 5-4" fill="none" stroke="#fff" stroke-width="1.2"/></svg>
        <span>Brent@Talvora.co.nz</span>
      </li>
    </ul>
  </section>

  <section class="card card-back" aria-label="Business card back">
    <h2 class="services-title">Service</h2>
    <div class="services-rule"></div>
    <ul class="services-list">
      <li class="service-item"><svg class="service-bullet" viewBox="0 0 12 12" aria-hidden="true"><circle cx="6" cy="6" r="5" fill="none" stroke="#ddd" stroke-width="1.2"/><circle cx="6" cy="6" r="2" fill="#ddd"/></svg><span>Suppliers of Talvora Louvres</span></li>
      <li class="service-item"><svg class="service-bullet" viewBox="0 0 12 12" aria-hidden="true"><circle cx="6" cy="6" r="5" fill="none" stroke="#ddd" stroke-width="1.2"/><circle cx="6" cy="6" r="2" fill="#ddd"/></svg><span>Aluminim Sable shutters</span></li>
      <li class="service-item"><svg class="service-bullet" viewBox="0 0 12 12" aria-hidden="true"><circle cx="6" cy="6" r="5" fill="none" stroke="#ddd" stroke-width="1.2"/><circle cx="6" cy="6" r="2" fill="#ddd"/></svg><span>Fennroll curtains</span></li>
      <li class="service-item"><svg class="service-bullet" viewBox="0 0 12 12" aria-hidden="true"><circle cx="6" cy="6" r="5" fill="none" stroke="#ddd" stroke-width="1.2"/><circle cx="6" cy="6" r="2" fill="#ddd"/></svg><span>Emberlyn outdoor heaters</span></li>
      <li class="service-item"><svg class="service-bullet" viewBox="0 0 12 12" aria-hidden="true"><circle cx="6" cy="6" r="5" fill="none" stroke="#ddd" stroke-width="1.2"/><circle cx="6" cy="6" r="2" fill="#ddd"/></svg><span>Corvane outdoor heaters</span></li>
    </ul>
  </section>
</main>
</body>
</html>
```